Brightmill Data Works

Our company is about IT hardwares and IT solutions. IT hardware such as PC, RAMS, storage and servers. IT solutions such as project management, BA. We are also selling new technology too.

Target Market(s)

Consumer, Small to Medium Business, Corporate

Requirements
Must have
• The business card must have the following:
• Name:
• Title:
• Contact Number:
• Email address:
• Website:
• Color: Must match the logo color upgrade

```html
<!DOCTYPE html>
<html lang="en">
<head>
<meta charset="utf-8">
<title>Brightmill Data Works – Business Card</title>
<link rel="stylesheet" href="https://fonts.googleapis.com/css2?family=Arimo:wght@400;700&display=swap">
<style>
  :root {
    --bg: #1b1b1e;
    --card-black: #060606;
    --orange-light: #e3a046;
    --orange-deep: #c8692a;
    --accent: #d9893a;
    --white: #ffffff;
    --ink: #111111;
  }
  * { margin: 0; padding: 0; box-sizing: border-box; }
  html, body {
    width: 1200px;
    height: 800px;
    overflow: hidden;
    background: var(--bg);
    font-family: "Arimo", Arial, sans-serif;
  }
  .stage {
    width: 1200px;
    height: 800px;
    display: flex;
    align-items: center;
    justify-content: center;
    gap: 60px;
  }
  .card {
    position: relative;
    width: 525px;
    height: 300px;
    box-shadow: 0 18px 40px rgba(0,0,0,0.45);
  }

  /* Front */
  .card--front {
    background: linear-gradient(160deg, var(--orange-light) 0%, var(--orange-deep) 100%);
    display: flex;
    align-items: center;
    justify-content: center;
  }
  .brand {
    display: flex;
    align-items: center;
    gap: 14px;
  }
  .brand__dot {
    width: 18px;
    height: 18px;
    border-radius: 50%;
    flex: none;
  }
  .brand__name {
    font-weight: 700;
    text-transform: uppercase;
    line-height: 1.05;
    letter-spacing: 0.5px;
  }
  .card--front .brand__dot { background: var(--ink); }
  .card--front .brand__name { color: var(--ink); font-size: 34px; }

  /* Back */
  .card--back {
    background: var(--card-black);
    color: var(--white);
  }
  .card--back .brand {
    position: absolute;
    left: 42px;
    top: 118px;
  }
  .card--back .brand__dot { background: var(--white); width: 14px; height: 14px; }
  .card--back .brand__name { color: var(--white); font-size: 25px; }

  .divider {
    position: absolute;
    left: 258px;
    top: 88px;
    width: 1px;
    height: 110px;
    background: linear-gradient(to bottom, transparent, var(--accent), transparent);
  }
  .contact {
    position: absolute;
    left: 282px;
    top: 74px;
  }
  .contact__name {
    font-weight: 700;
    font-size: 15px;
    letter-spacing: 0.3px;
    text-transform: uppercase;
  }
  .contact__title {
    color: var(--accent);
    font-size: 13px;
    margin-bottom: 10px;
  }
  .contact__list { list-style: none; }
  .contact__item {
    display: flex;
    align-items: center;
    gap: 8px;
    font-size: 12px;
    line-height: 20px;
  }
  .contact__icon { width: 11px; height: 11px; flex: none; }
  .address {
    position: absolute;
    left: 42px;
    right: 30px;
    bottom: 30px;
    font-size: 12.5px;
    text-align: right;
  }
</style>
</head>
<body>
<main class="stage">
  <section class="card card--front" aria-label="Business card front">
    <div class="brand">
      <span class="brand__dot"></span>
      <span class="brand__name">Brightmill<br>Data Works</span>
    </div>
  </section>

  <section class="card card--back" aria-label="Business card back">
    <div class="brand">
      <span class="brand__dot"></span>
      <span class="brand__name">Brightmill<br>Data Works</span>
    </div>

    <div class="divider"></div>

    <div class="contact">
      <p class="contact__name">Dara Quill</p>
      <p class="contact__title">Manager</p>
      <ul class="contact__list">
        <li class="contact__item">
          <svg class="contact__icon" viewBox="0 0 12 12" aria-hidden="true">
            <path fill="#d9893a" d="M2.5 1h2l1 2.5-1.3 1a6 6 0 0 0 3.3 3.3l1-1.3L11 7.5v2A1.5 1.5 0 0 1 9.5 11 8.5 8.5 0 0 1 1 2.5 1.5 1.5 0 0 1 2.5 1z"/>
          </svg>
          555-201-4837
        </li>
        <li class="contact__item">
          <svg class="contact__icon" viewBox="0 0 12 12" aria-hidden="true">
            <rect x="0.5" y="2" width="11" height="8" fill="#d9893a"/>
            <path d="M0.5 2.5 6 6.5l5.5-4" fill="none" stroke="#060606" stroke-width="1"/>
          </svg>
          info@brightmilldata.com
        </li>
        <li class="contact__item">
          <svg class="contact__icon" viewBox="0 0 12 12" aria-hidden="true">
            <circle cx="6" cy="6" r="5.2" fill="#d9893a"/>
            <path d="M0.8 6h10.4M6 0.8c-2.2 2.6-2.2 7.8 0 10.4M6 0.8c2.2 2.6 2.2 7.8 0 10.4" fill="none" stroke="#060606" stroke-width="0.7"/>
          </svg>
          www.brightmilldata.com
        </li>
      </ul>
    </div>

    <p class="address">PO BOX 48 Larchfield Lane, 7th street Halden</p>
  </section>
</main>
</body>
</html>
```